Marta's Dwellings website

We need a simple website for our property investment business in the UK. We basically need our contact details and brief description.We have the company logo already done (via ArtFlockly) so please use these:https://drive.google.com/drive/folders/1szJ3iRhelElZ40NIFT7w-c14MaY3Y_oV?usp=sharingYou could use some stock photos of UK houses for now.Let me know when to provide more detailed descriptions, etc

Coding

Coded - Design and coding required

Number of Pages Required

1 page

Colors

Designer to choose colors to be used in the design.

```html
<!DOCTYPE html>
<html lang="en">
<head>
<meta charset="utf-8">
<title>Marta's Dwellings — Property Investment in the UK</title>
<link href="https://fonts.googleapis.com/css2?family=Jost:wght@400;500;600;700&family=Poppins:wght@300;400;500;600&display=swap" rel="stylesheet">
<style>
:root{
  --navy:#1f3f8f;
  --blue:#2456a6;
  --ink:#1d2230;
  --heading:#2f3a55;
  --text:#555a66;
  --orange:#f7901e;
  --grey-bg:#efefef;
  --cream:#fffdf3;
  --footer:#101114;
  --white:#ffffff;
}
*{margin:0;padding:0;box-sizing:border-box}
html,body{width:1200px;height:4208px;overflow:hidden;background:var(--white)}
body{font-family:"Poppins",sans-serif;color:var(--text);position:relative}
.abs{position:absolute}
.h-font{font-family:"Jost",sans-serif}

/* Hero */
.hero{position:absolute;left:0;top:0;width:1200px;height:780px;
  background:linear-gradient(180deg,#1e3f78 0%,#3f6a9c 22%,#6b7c6e 48%,#4f6a3a 66%,#5d6368 80%,#3a4a44 100%)}
.hero-shade{position:absolute;inset:0;background:linear-gradient(180deg,rgba(14,30,70,.55),rgba(14,30,70,.1) 40%,rgba(0,0,0,.15))}
.brand{left:144px;top:30px;width:190px;text-align:center;color:var(--white)}
.brand-mark{width:22px;height:22px;border:3px solid var(--white);margin:0 auto 10px}
.brand-name{font-family:"Jost",sans-serif;font-size:15px;letter-spacing:5px;font-weight:400;text-transform:uppercase}
.call{left:516px;top:38px;color:var(--white);font-family:"Jost",sans-serif;font-size:22px;display:flex;align-items:center;gap:12px}
.call-icon{width:38px;height:38px;border:2px solid var(--white);border-radius:50%;display:flex;align-items:center;justify-content:center}
.search{left:789px;top:34px;width:266px;height:36px;background:var(--white);border-radius:18px;font-size:12px;color:#888;padding:9px 16px;display:flex;justify-content:space-between}
.nav{left:438px;top:96px;width:617px;display:flex;justify-content:space-between;font-family:"Jost",sans-serif;font-weight:600;font-size:19px;color:var(--white);text-transform:uppercase}
.hero-title{left:0;width:1200px;top:305px;text-align:center;color:var(--white);font-family:"Jost",sans-serif;font-weight:600;font-size:70px;line-height:1;text-shadow:0 2px 8px rgba(0,0,0,.35)}
.hero-sub{left:0;width:1200px;top:396px;text-align:center;color:var(--white);font-family:"Jost",sans-serif;font-size:26px}
.btn-orange{background:var(--orange);color:var(--white);font-family:"Jost",sans-serif;font-weight:600;border-radius:24px;text-align:center;text-transform:uppercase}
.hero-btn{left:501px;top:462px;width:196px;height:44px;line-height:44px;font-size:18px}
.arrow-round{width:40px;height:40px;border-radius:50%;background:rgba(0,0,0,.35);display:flex;align-items:center;justify-content:center}
.hero-curve{left:0;top:690px}

/* Section heads */
.sec-title{left:0;width:1200px;text-align:center;font-family:"Jost",sans-serif;font-weight:500;font-size:38px;color:var(--ink);text-transform:uppercase;letter-spacing:.5px}
.sec-rule{left:570px;width:60px;height:3px;background:var(--navy)}

/* Services */
.service{width:230px;text-align:center}
.service svg{display:block;margin:0 auto}
.service h3{font-family:"Jost",sans-serif;font-weight:400;font-size:21px;color:var(--ink);margin-top:30px}
.service p{font-size:13px;line-height:24px;margin-top:14px;color:var(--text)}
.service .more{margin-top:14px;color:#555;font-size:14px}

/* Welcome */
.welcome{left:0;top:1288px;width:1200px;height:614px;background:linear-gradient(160deg,#5d8fd0 0%,#9cc0e6 30%,#a24a33 45%,#8a4a3a 62%,#6f8a4a 82%,#8c8f92 100%)}
.welcome-frame{left:572px;top:1404px;width:483px;height:376px;border:2px solid var(--white)}
.welcome-card{left:582px;top:1414px;width:463px;height:356px;background:var(--white);padding:34px 36px}
.welcome-card h2{font-family:"Jost",sans-serif;font-weight:500;color:var(--ink);text-transform:uppercase;line-height:1.2}
.welcome-card h2 .small{font-size:28px;display:block}
.welcome-card h2 .big{font-size:38px;display:block;font-weight:600}
.welcome-card p{font-size:13px;line-height:28.5px;margin-top:14px;color:var(--text)}
.btn-outline{display:inline-block;border:2px solid var(--navy);color:var(--navy);border-radius:22px;font-family:"Jost",sans-serif;font-weight:500;text-transform:uppercase}
.welcome-card .btn-outline{margin-top:20px;width:136px;height:43px;line-height:39px;text-align:center;font-size:15px}

/* Investments */
.invest{left:0;top:1902px;width:1200px;height:730px;background:var(--grey-bg)}
.card{top:2138px;width:294px;height:377px;background:var(--cream);box-shadow:0 1px 4px rgba(0,0,0,.18)}
.card-photo{height:188px}
.card-body{padding:20px 15px 0}
.card-body h3{font-family:"Jost",sans-serif;font-weight:400;font-size:19px;color:var(--ink)}
.card-body p{font-size:12px;line-height:24px;margin-top:10px}
.card-foot{position:absolute;left:0;bottom:0;width:100%;border-top:1px solid #e6e3d6;padding:10px 12px;font-size:12px;color:#333;display:flex;align-items:center;gap:7px}

/* Newsletter */
.newsletter{left:0;top:2632px;width:1200px;height:321px;background:linear-gradient(90deg,#2352a3,#2a5fb2 50%,#2352a3)}
.newsletter h2{position:absolute;left:0;width:1200px;top:60px;text-align:center;color:var(--white);font-family:"Jost",sans-serif;font-weight:500;font-size:40px}
.newsletter p{position:absolute;left:0;width:1200px;top:134px;text-align:center;color:#e6ecf7;font-size:18px}
.field{background:var(--white);border-radius:21px;height:40px;font-size:13px;color:#444;padding:11px 22px}

/* Blog */
.blog{left:0;top:2953px;width:1200px;height:648px;background:#fbfbfc}
.blog-photo{left:152px;top:3148px;width:400px;height:307px;border:4px solid var(--white);box-shadow:0 4px 14px rgba(0,0,0,.3);background:linear-gradient(180deg,#aac4e0 0%,#d8e2ec 35%,#b06a3e 50%,#8a5c3c 66%,#6f7a56 78%,#777c82 100%)}
.blog-title{left:607px;top:3150px;width:460px;font-family:"Jost",sans-serif;font-weight:600;font-size:29px;line-height:37px;color:var(--heading);text-transform:uppercase}
.blog-meta{left:607px;top:3251px;font-size:12.5px;color:var(--navy);font-style:italic;display:flex;gap:28px}
.blog-text{left:607px;top:3290px;width:450px;font-size:12px;line-height:28px}
.blog-btn{left:609px;top:3421px;width:106px;height:29px;line-height:25px;text-align:center;font-size:11px;font-weight:600;color:var(--ink);border-color:var(--ink)}

/* Partners */
.partners{left:0;top:3601px;width:1200px;height:114px;background:var(--grey-bg);display:flex;justify-content:center;align-items:center;gap:62px}
.partner{width:100px;height:30px;background:#c9cacc;border-radius:3px}

/* Footer */
.footer{left:0;top:3715px;width:1200px;height:493px;background:var(--footer);color:#e8e8e8}
.footer h4{font-family:"Jost",sans-serif;font-weight:600;font-size:18px;color:var(--white);text-transform:uppercase}
.f-contact{left:124px;top:70px;width:300px;font-size:13.5px;line-height:22px}
.f-row{display:flex;gap:12px;margin-top:14px}
.f-row svg{flex:none;margin-top:4px}
.f-links{left:469px;top:70px;font-size:13.5px}
.f-links li{list-style:none;line-height:31px}
.f-quote{left:640px;top:70px;width:444px;font-size:12.5px;line-height:22px}
.q-field{border:1px solid #7a7b80;height:40px;font-size:10px;padding:13px 12px;color:#ddd}
.q-submit{background:#1f4aa8;color:var(--white);height:40px;line-height:40px;text-align:center;font-family:"Jost",sans-serif;font-weight:600;font-size:16px}
.copyright{left:120px;top:426px;font-size:13.5px}
.social{left:984px;top:416px;display:flex;gap:6px}
.social span{width:25px;height:25px;border:1.5px solid #cfcfcf;border-radius:50%}
</style>
</head>
<body>

<!-- Hero -->
<section class="hero" role="img" aria-label="Photograph of a quiet UK street with timber-framed houses and parked cars">
  <div class="hero-shade"></div>
</section>
<div class="abs brand"><div class="brand-mark"></div><div class="brand-name">Marta's Dwellings</div></div>
<div class="abs call">Call (555) 480-1937
  <span class="call-icon"><svg width="18" height="18" viewBox="0 0 24 24" fill="none" stroke="#fff" stroke-width="2"><path d="M5 3h4l2 5-3 2a12 12 0 0 0 6 6l2-3 5 2v4a2 2 0 0 1-2 2A17 17 0 0 1 3 5a2 2 0 0 1 2-2z"/></svg></span>
</div>
<div class="abs search"><span>Search</span><svg width="12" height="12" viewBox="0 0 24 24" fill="none" stroke="#555" stroke-width="3"><circle cx="10" cy="10" r="7"/><path d="M15 15l6 6"/></svg></div>
<nav class="abs nav"><span>Home</span><span>About Us</span><span>Our Services</span><span>Projects</span><span>Blog</span><span>Contact</span></nav>
<h1 class="abs hero-title">MARTA'S DWELLINGS</h1>
<div class="abs hero-sub">our property investment business in the UK</div>
<div class="abs btn-orange hero-btn">Get More Info</div>
<div class="abs arrow-round" style="left:102px;top:342px"><svg width="14" height="14" viewBox="0 0 24 24" fill="none" stroke="#fff" stroke-width="2"><path d="M15 4l-8 8 8 8"/></svg></div>
<div class="abs arrow-round" style="left:1053px;top:342px"><svg width="14" height="14" viewBox="0 0 24 24" fill="none" stroke="#fff" stroke-width="2"><path d="M9 4l8 8-8 8"/></svg></div>
<svg class="abs hero-curve" width="1200" height="92" viewBox="0 0 1200 92">
  <path d="M0 92 L0 80 Q600 -40 1200 80 L1200 92 Z" fill="#fff"/>
  <path d="M40 92 Q600 -20 1160 92" fill="none" stroke="#1f3f8f" stroke-width="5"/>
</svg>

<!-- Services -->
<h2 class="abs sec-title" style="top:806px">Our Services</h2>
<div class="abs sec-rule" style="top:882px"></div>

<div class="abs service" style="left:120px;top:935px">
  <svg width="72" height="72" viewBox="0 0 72 72" fill="none" stroke="#1f4aa8" stroke-width="2.5"><path d="M8 32 L36 10 L64 32"/><path d="M14 28v34h44V28"/><rect x="20" y="36" width="12" height="10"/><rect x="40" y="36" width="12" height="10"/><circle cx="48" cy="56" r="8" fill="#fff"/><path d="M48 52v8"/></svg>
  <h3>Property Investment</h3>
  <p>Sed ut perspiciatis unde omnis iste natus error sit voluptatem accusantium doloremque laudantium, totam</p>
  <div class="more">&#8964;</div>
</div>
<div class="abs service" style="left:357px;top:935px">
  <svg width="72" height="72" viewBox="0 0 72 72" fill="none" stroke="#1f4aa8" stroke-width="2.5"><path d="M10 62h52"/><rect x="16" y="40" width="8" height="22"/><rect x="32" y="30" width="8" height="32"/><rect x="48" y="18" width="8" height="44"/><path d="M12 30 L28 18 L40 24 L60 8"/></svg>
  <h3>Nemo enim ipsam</h3>
  <p>Sed ut perspiciatis unde omnis iste natus error sit voluptatem accusantium doloremque laudantium, totam</p>
  <div class="more">&#8964;</div>
</div>
<div class="abs service" style="left:595px;top:935px">
  <svg width="72" height="72" viewBox="0 0 72 72" fill="none" stroke="#1f4aa8" stroke-width="2.5"><path d="M6 40 L26 24 L46 40"/><path d="M12 36v26h28V36"/><rect x="22" y="46" width="8" height="16"/><path d="M50 8l12 5v10c0 8-5 13-12 16-7-3-12-8-12-16V13z" fill="#fff"/><path d="M45 22l4 4 7-8"/></svg>
  <h3>UK Houses</h3>
  <p>Sed ut perspiciatis unde omnis iste natus error sit voluptatem accusantium doloremque laudantium, totam</p>
  <div class="more">&#8964;</div>
</div>
<div class="abs service" style="left:834px;top:935px">
  <svg width="72" height="72" viewBox="0 0 72 72" fill="none" stroke="#1f4aa8" stroke-width="2.5"><rect x="8" y="12" width="50" height="46" rx="3"/><path d="M8 24h50M18 6v10M48 6v10M16 32h34M16 40h34M16 48h24M24 24v30M34 24v30M44 24v20"/><circle cx="56" cy="56" r="10" fill="#fff"/><path d="M51 56l4 4 6-7"/></svg>
  <h3>Nemo enim ipsam</h3>
  <p>Sed ut perspiciatis unde omnis iste natus error sit voluptatem accusantium doloremque laudantium, totam</p>
  <div class="more">&#8964;</div>
</div>

<!-- Welcome -->
<section class="abs welcome" role="img" aria-label="Photograph of new-build red brick houses along a sunny residential road"></section>
<div class="abs welcome-frame"></div>
<div class="abs welcome-card">
  <h2><span class="small">Welcome to</span><span class="big">Marta's Dwellings</span></h2>
  <p>Sed ut perspiciatis unde omnis iste natus error sit voluptatem acantium doloremque laudantium, totam rem aperiam, eaque ipsa quae ab illo inventore veritatis et quasi architecto beatae vitae dicta sunt explicabo. Nemo enim ipsam voluptatem quia voluptas sit aspernatur aut odit aut fugit, sed quia conseq</p>
  <span class="btn-outline">Read More</span>
</div>

<!-- Property investment -->
<section class="abs invest"></section>
<h2 class="abs sec-title" style="top:2002px">Our Property Investment</h2>
<div class="abs sec-rule" style="top:2074px"></div>

<article class="abs card" style="left:131px">
  <div class="card-photo" role="img" aria-label="Photo of a small model house on a desk beside paperwork" style="background:linear-gradient(135deg,#8fa3b8,#dfe4ea 50%,#b53a32 85%)"></div>
  <div class="card-body"><h3>Sed ut perspiciatis unde</h3><p>Nemo enim ipsam voluptatem quia voluptas sit aspernatur aut odit aut fugit, sed quia consequuntur magni dolores eos</p></div>
  <div class="card-foot"><svg width="9" height="12" viewBox="0 0 12 16"><path d="M6 0a6 6 0 0 1 6 6c0 4-6 10-6 10S0 10 0 6a6 6 0 0 1 6-6z" fill="#333"/><circle cx="6" cy="6" r="2" fill="#fff"/></svg>Unit 7, Orchard Court, 14-16 Millbr..</div>
</article>
<article class="abs card" style="left:451px">
  <div class="card-photo" role="img" aria-label="Photo of a model house with a calculator and stacked coins" style="background:linear-gradient(135deg,#c8b24a,#e2b08a 45%,#4f6f4e 100%)"></div>
  <div class="card-body"><h3>Sed ut perspiciatis unde</h3><p>Nemo enim ipsam voluptatem quia voluptas sit aspernatur aut odit aut fugit, sed quia consequuntur magni dolores eos</p></div>
  <div class="card-foot"><svg width="9" height="12" viewBox="0 0 12 16"><path d="M6 0a6 6 0 0 1 6 6c0 4-6 10-6 10S0 10 0 6a6 6 0 0 1 6-6z" fill="#333"/><circle cx="6" cy="6" r="2" fill="#fff"/></svg>Unit 7, Orchard Court, 14-16 Millbr..</div>
</article>
<article class="abs card" style="left:771px">
  <div class="card-photo" role="img" aria-label="Photo of a laptop and mortgage form with a small model house" style="background:linear-gradient(135deg,#2c3440,#6b7888 50%,#c9d1dc 100%)"></div>
  <div class="card-body"><h3>Sed ut perspiciatis unde</h3><p>Nemo enim ipsam voluptatem quia voluptas sit aspernatur aut odit aut fugit, sed quia consequuntur magni dolores eos</p></div>
  <div class="card-foot"><svg width="9" height="12" viewBox="0 0 12 16"><path d="M6 0a6 6 0 0 1 6 6c0 4-6 10-6 10S0 10 0 6a6 6 0 0 1 6-6z" fill="#333"/><circle cx="6" cy="6" r="2" fill="#fff"/></svg>Unit 7, Orchard Court, 14-16 Millbr..</div>
</article>

<!-- Newsletter -->
<section class="abs newsletter">
  <h2>Sign up for newsletter</h2>
  <p>Sed ut perspiciatis unde omnis iste natus error sit voluptatem accusantium doloremque</p>
  <div class="abs field" style="left:229px;top:200px;width:269px">Your First Name</div>
  <div class="abs field" style="left:511px;top:200px;width:268px">Your email</div>
  <div class="abs btn-orange" style="left:797px;top:200px;width:175px;height:40px;line-height:40px;font-size:17px">Subscribe</div>
</section>

<!-- Blog -->
<section class="abs blog"></section>
<h2 class="abs sec-title" style="top:3032px;left:-13px">Latest Blog</h2>
<div class="abs blog-photo" role="img" aria-label="Photograph of brick family homes on a suburban street"></div>
<h3 class="abs blog-title">Quis autem vel eum iure reprehenderit qui in</h3>
<div class="abs blog-meta"><span>&#9638; March 25, 2019</span><span>&#9675; 2 comments</span></div>
<p class="abs blog-text">Sed ut perspiciatis unde omnis iste natus error sit voluptatem accusntium doloremque laudantium, totam rem aperiam, eaque ipsa quae ab illo inventore veritatis et quasi architecto beatae vitae dicta sunt explicabo. Nemo enim ipsam voluptatem quia voluptas sit aspernatur</p>
<span class="abs btn-outline blog-btn">Learn More</span>
<svg class="abs" style="left:54px;top:3268px" width="30" height="54" viewBox="0 0 30 54" fill="none" stroke="#2a4ea0" stroke-width="2"><path d="M28 2L2 27l26 25"/></svg>
<svg class="abs" style="left:1122px;top:3268px" width="30" height="54" viewBox="0 0 30 54" fill="none" stroke="#2a4ea0" stroke-width="2"><path d="M2 2l26 25L2 52"/></svg>

<!-- Partners -->
<section class="abs partners" aria-label="Partner companies">
  <span class="partner"></span><span class="partner"></span><span class="partner"></span><span class="partner"></span><span class="partner"></span><span class="partner"></span>
</section>

<!-- Footer -->
<footer class="abs footer">
  <div class="abs f-contact">
    <h4>Contact Us</h4>
    <div class="f-row" style="margin-top:30px"><svg width="10" height="14" viewBox="0 0 12 16"><path d="M6 0a6 6 0 0 1 6 6c0 4-6 10-6 10S0 10 0 6a6 6 0 0 1 6-6z" fill="#ddd"/><circle cx="6" cy="6" r="2" fill="#101114"/></svg><span>Unit 7, Orchard Court, 14-16 Millbrook Road, Ashford Vale, Westshire, United Kingdom, AV4 9QT</span></div>
    <div class="f-row"><svg width="12" height="12" viewBox="0 0 24 24"><path d="M5 3h4l2 5-3 2a12 12 0 0 0 6 6l2-3 5 2v4a2 2 0 0 1-2 2A17 17 0 0 1 3 5a2 2 0 0 1 2-2z" fill="#ddd"/></svg><span>Phone:<br>888.3172.0649</span></div>
    <div class="f-row"><svg width="12" height="10" viewBox="0 0 24 18"><rect width="24" height="18" fill="#ddd"/><path d="M0 0l12 9 12-9" fill="none" stroke="#101114" stroke-width="2"/></svg><span>Email: hello@martasdwellings.example</span></div>
    <div style="margin:14px 0 0 27px;font-style:italic">Contact - Marta Lise Ander</div>
  </div>
  <div class="abs f-links">
    <h4>Quick Links</h4>
    <ul style="margin-top:20px"><li>Home</li><li>About Us</li><li>Our Services</li><li>Blog</li><li>Contact Us</li></ul>
  </div>
  <div class="abs f-quote">
    <h4>Get a Quote</h4>
    <p style="margin-top:16px">Sed ut perspiciatis unde omnis iste natus error sit voluptatem accusantium doloremque laudantium</p>
    <div class="abs q-field" style="left:6px;top:140px;width:206px">Name</div>
    <div class="abs q-field" style="left:232px;top:140px;width:206px">E - Mail</div>
    <div class="abs q-field" style="left:6px;top:196px;width:206px">Phone No</div>
    <div class="abs q-submit" style="left:232px;top:196px;width:208px">SUBMIT</div>
  </div>
  <div class="abs copyright">&copy; 2019 Marta's Dwellings. All Rights Reserved.</div>
  <div class="abs social" aria-label="Social links"><span></span><span></span><span></span><span></span></div>
</footer>

</body>
</html>
```